KLV Plant Services

We are a heavy diesel mechanical business with additional air con certificates, remapping engine rebuilt

Contact Information for Business Card

Company Name, Director Name, Managing Director, Contact details, email and website

Font styles to use
Serif
Script

```html
<!DOCTYPE html>
<html lang="en">
<head>
<meta charset="utf-8">
<title>KLV Plant Services – Business Card</title>
<link href="https://fonts.googleapis.com/css2?family=Noto+Serif:wght@400;700&display=swap" rel="stylesheet">
<style>
  :root {
    --bg: #d6d6d6;
    --navy: #16125f;
    --paper: #f1f1f0;
    --ink: #1c1c24;
    --illustration: #141414;
  }
  html, body {
    margin: 0;
    width: 1200px;
    height: 1051px;
    overflow: hidden;
    background: var(--bg);
    font-family: "Noto Serif", serif;
  }
  .canvas {
    position: relative;
    width: 1200px;
    height: 1051px;
  }
  .card {
    position: absolute;
    left: 250px;
    width: 700px;
    height: 400px;
    box-sizing: border-box;
    box-shadow: 0 18px 40px rgba(0,0,0,0.18);
    overflow: hidden;
  }
  .card-front {
    top: 90px;
    background: var(--paper);
    border-bottom: 5px solid var(--navy);
  }
  .card-back {
    top: 560px;
    background: var(--navy);
  }
  .brand-small {
    position: absolute;
    left: 48px;
    top: 48px;
    display: flex;
    align-items: center;
    gap: 12px;
    color: var(--navy);
    font-weight: 700;
    font-size: 26px;
    line-height: 1.05;
  }
  .brand-ring {
    width: 26px;
    height: 26px;
    border: 3px solid var(--navy);
    border-radius: 50%;
    flex: none;
  }
  .address {
    position: absolute;
    left: 48px;
    top: 150px;
    margin: 0;
    font-size: 17px;
    line-height: 1.3;
    color: var(--ink);
  }
  .contacts {
    position: absolute;
    left: 48px;
    top: 218px;
    margin: 0;
    padding: 0;
    list-style: none;
    font-size: 17px;
    line-height: 1.45;
    color: var(--ink);
  }
  .contacts li {
    display: flex;
    align-items: center;
    gap: 9px;
  }
  .contacts svg {
    width: 14px;
    height: 14px;
    fill: var(--navy);
  }
  .person {
    position: absolute;
    right: 40px;
    top: 60px;
    text-align: right;
    color: var(--navy);
  }
  .person-name {
    margin: 0;
    font-weight: 700;
    font-size: 25px;
    letter-spacing: 0.5px;
  }
  .person-role {
    margin: 2px 0 0;
    font-size: 17px;
  }
  .name-tab {
    position: absolute;
    right: 0;
    top: 62px;
    width: 18px;
    height: 56px;
    background: var(--navy);
  }
  .excavator-art {
    position: absolute;
    right: 0;
    bottom: 0;
    width: 360px;
    height: 210px;
    background: linear-gradient(160deg, #2b2b2b, var(--illustration));
    clip-path: polygon(0 45%, 70% 0, 100% 10%, 100% 100%, 8% 100%);
  }
  .brand-large {
    position: absolute;
    inset: 0;
    display: flex;
    align-items: center;
    justify-content: center;
    gap: 22px;
    color: #ffffff;
    font-weight: 700;
    font-size: 52px;
  }
  .brand-large .brand-ring {
    width: 54px;
    height: 54px;
    border: 5px solid #ffffff;
  }
</style>
</head>
<body>
<main class="canvas">
  <section class="card card-front">
    <div class="brand-small"><span class="brand-ring"></span><span>KLV<br>Plant Services</span></div>
    <p class="address">Your address, City<br>State, Zip 1234</p>
    <ul class="contacts">
      <li><svg viewBox="0 0 16 16"><path d="M3 1l3 3-2 2c1 2 3 4 5 5l2-2 3 3-2 3C7 15 1 9 0 4z"/></svg>123 456 789</li>
      <li><svg viewBox="0 0 16 16"><path d="M0 3h16v10H0zM1 4l7 5 7-5v1L8 10 1 5z" fill-rule="evenodd"/></svg>info@klvplant.com</li>
      <li><svg viewBox="0 0 16 16"><circle cx="8" cy="8" r="7.5"/></svg>www.klvplant.com</li>
    </ul>
    <div class="person">
      <p class="person-name">DANIEL HART</p>
      <p class="person-role">Managing Director</p>
    </div>
    <div class="name-tab"></div>
    <div class="excavator-art" role="img" aria-label="Black silhouette illustration of an excavator arm and bucket"></div>
  </section>
  <section class="card card-back">
    <div class="brand-large"><span class="brand-ring"></span><span>KLV Plant Services</span></div>
  </section>
</main>
</body>
</html>
```